Dusty Spur Outfitters Home Page

I need a logo and page design for my home page, maybe some background color suggestions to go with it. I want the logo to project "vintage" and "western wear" but not be your typical trite western saddle and gun type thing.
http://www.dustyspuroutfitters.example/store/cart.php
Not looking for page coding just logo and other design elements to lay in over the site's template to make it "pop"
Reason: Have to finalize the design.
Target Market(s)
My customers are 70/30 men to women.
Industry/Entity Type
Gun

```html
<!DOCTYPE html>
<html lang="en">
<head>
<meta charset="utf-8">
<title>Dusty Spur Outfitters Header Options</title>
<link rel="stylesheet" href="https://fonts.googleapis.com/css2?family=Lato:wght@700;900&family=Norican&display=swap">
<style>
  :root {
    --canvas-tan: #d9c9ab;
    --band-teal: #3a9aab;
    --band-teal-dark: #2d8292;
    --board-charcoal: #2a2a29;
    --board-charcoal-light: #3a3a37;
    --cream: #e8dcbf;
    --search-fill: #e6d9bd;
    --ink: #2a2622;
    --speck: rgba(232, 220, 191, 0.16);
    --scuff: rgba(0, 0, 0, 0.28);
    --variant-teal: #5fb3b3;
    --variant-gold: #e2c27a;
    --variant-orange: #e0892e;
    --variant-coral: #d2573f;
  }
  * { margin: 0; padding: 0; box-sizing: border-box; }
  html, body { width: 1200px; height: 1000px; overflow: hidden; }
  body {
    position: relative;
    background:
      repeating-linear-gradient(45deg, rgba(255,255,255,0.05) 0 2px, rgba(0,0,0,0.03) 2px 4px),
      repeating-linear-gradient(-45deg, rgba(255,255,255,0.03) 0 1px, transparent 1px 3px),
      var(--canvas-tan);
    font-family: "Lato", sans-serif;
  }
  .header-option {
    position: absolute;
    left: 0;
    width: 1200px;
    height: 166px;
    background:
      repeating-linear-gradient(90deg, rgba(0,0,0,0.06) 0 3px, transparent 3px 17px, rgba(255,255,255,0.05) 17px 19px, transparent 19px 41px),
      linear-gradient(180deg, var(--band-teal) 0%, var(--band-teal-dark) 100%);
    box-shadow: 0 4px 6px rgba(60, 45, 25, 0.35);
  }
  .header-option:nth-of-type(1) { top: 74px; --variant: var(--variant-teal); --name-colour: #d9e6d6; }
  .header-option:nth-of-type(2) { top: 304px; --variant: var(--variant-gold); --name-colour: #eddcb0; }
  .header-option:nth-of-type(3) { top: 534px; --variant: var(--variant-orange); --name-colour: #f0cf92; }
  .header-option:nth-of-type(4) { top: 764px; --variant: var(--variant-coral); --name-colour: #ecd2b8; }
  .header-board {
    position: absolute;
    left: 0; right: 0;
    top: 15px; bottom: 19px;
    background:
      radial-gradient(circle at 3px 4px, var(--speck) 0 1px, transparent 1.5px) 0 0 / 23px 19px,
      radial-gradient(circle at 9px 11px, rgba(232,220,191,0.1) 0 1px, transparent 1.5px) 0 0 / 37px 29px,
      radial-gradient(circle at 5px 7px, var(--scuff) 0 3px, transparent 4px) 0 0 / 53px 41px,
      repeating-linear-gradient(100deg, transparent 0 31px, rgba(255,255,255,0.035) 31px 32px, transparent 32px 67px),
      repeating-linear-gradient(75deg, transparent 0 47px, rgba(0,0,0,0.2) 47px 49px, transparent 49px 89px),
      radial-gradient(ellipse at 20% 40%, var(--board-charcoal-light), transparent 55%),
      radial-gradient(ellipse at 60% 30%, #333331, transparent 45%),
      radial-gradient(ellipse at 85% 70%, var(--board-charcoal-light), transparent 50%),
      var(--board-charcoal);
    clip-path: polygon(0 7%, 3% 4%, 6% 6%, 9% 3%, 13% 5%, 17% 2%, 21% 4%, 25% 2%, 29% 5%, 33% 3%, 37% 6%, 41% 2%, 45% 4%, 49% 1%, 53% 4%, 57% 2%, 61% 5%, 65% 3%, 69% 6%, 73% 2%, 77% 4%, 81% 1%, 85% 4%, 89% 2%, 93% 5%, 97% 3%, 100% 6%,
      100% 94%, 97% 97%, 93% 95%, 89% 98%, 85% 96%, 81% 99%, 77% 96%, 73% 98%, 69% 95%, 65% 97%, 61% 94%, 57% 98%, 53% 96%, 49% 99%, 45% 96%, 41% 98%, 37% 95%, 33% 97%, 29% 94%, 25% 98%, 21% 96%, 17% 99%, 13% 96%, 9% 98%, 5% 95%, 0 97%);
  }
  .brand-mark {
    position: absolute;
    left: 60px;
    top: 0;
    width: 406px;
    height: 166px;
    display: flex;
    align-items: center;
    justify-content: center;
    gap: 12px;
  }
  .brand-dot {
    width: 18px; height: 18px;
    border-radius: 50%;
    background: var(--variant);
    flex: none;
  }
  .brand-name {
    font-family: "Lato", sans-serif;
    font-weight: 900;
    font-size: 31px;
    color: var(--name-colour);
    letter-spacing: 0.5px;
    white-space: nowrap;
  }
  .tagline {
    position: absolute;
    left: 476px;
    top: 88px;
    font-family: "Norican", cursive;
    font-size: 25px;
    line-height: 30px;
    letter-spacing: 0.9px;
    color: var(--cream);
    white-space: nowrap;
  }
  .site-search {
    position: absolute;
    left: 901px;
    top: 51px;
    display: flex;
    align-items: center;
    gap: 11px;
  }
  .search-field {
    width: 173px;
    height: 30px;
    border-radius: 15px;
    background: var(--search-fill);
    color: var(--ink);
    font-weight: 700;
    font-size: 17px;
    line-height: 30px;
    padding-left: 17px;
  }
  .search-go {
    color: var(--cream);
    font-weight: 700;
    font-size: 17px;
  }
</style>
</head>
<body>
  <header class="header-option">
    <div class="header-board"></div>
    <div class="brand-mark"><span class="brand-dot"></span><span class="brand-name">Dusty Spur Outfitters</span></div>
    <p class="tagline">Brand-New Retro Styled Western Wear</p>
    <div class="site-search"><span class="search-field">Search...</span><span class="search-go">GO!</span></div>
  </header>
  <header class="header-option">
    <div class="header-board"></div>
    <div class="brand-mark"><span class="brand-dot"></span><span class="brand-name">Dusty Spur Outfitters</span></div>
    <p class="tagline">Brand-New Retro Styled Western Wear</p>
    <div class="site-search"><span class="search-field">Search...</span><span class="search-go">GO!</span></div>
  </header>
  <header class="header-option">
    <div class="header-board"></div>
    <div class="brand-mark"><span class="brand-dot"></span><span class="brand-name">Dusty Spur Outfitters</span></div>
    <p class="tagline">Brand-New Retro Styled Western Wear</p>
    <div class="site-search"><span class="search-field">Search...</span><span class="search-go">GO!</span></div>
  </header>
  <header class="header-option">
    <div class="header-board"></div>
    <div class="brand-mark"><span class="brand-dot"></span><span class="brand-name">Dusty Spur Outfitters</span></div>
    <p class="tagline">Brand-New Retro Styled Western Wear</p>
    <div class="site-search"><span class="search-field">Search...</span><span class="search-go">GO!</span></div>
  </header>
</body>
</html>
```